Clear Plastic Card Design

I am looking to have a business card designed from my logo icon. I am looking to match the style of a different business card I have attached in the files.
Looking for a card that is plastic, with layers of transparency in the shape of my logo icon (also attached in the files) - not a circle like the other card. The winning design will incorporate the red icon logo on the front and back and include the charity's name, "Light for the Weary Souls" in the same or similar font, as well as an email and phone number. For now, use the email: email@lightfortheweary-mail.org and the phone number 555-382-7194.
We like how the sample business card has transparency, partial and full opacity layers and a matching color scheme. Files will need to be in vector so that our business card printing company can work with it.
UPDATE:
We've some excellent designs in, thank you everyone! I got an early review from the owner, and he requested a minor redirect to find his perfect design. He wants the design to stand out by NOT being a rectangle. Try instead a circle, square, or best yet - something that falls in the outline of the logo icon, either fully or partially. Thank you, everyone!
Light for the Weary Souls text should be incorporated as well as a phone and email.

```html
<!DOCTYPE html>
<html lang="en">
<head>
<meta charset="utf-8">
<title>Light for the Weary Souls – Business Card</title>
<link rel="stylesheet" href="https://fonts.googleapis.com/css2?family=Questrial&family=Arimo&display=swap">
<style>
  :root {
    --page-bg: #e9e4de;
    --card-front: #f3f1ee;
    --card-front-edge: #d9d3cc;
    --ink-dark: #2b2523;
    --brand-red: #d0322a;
    --back-red-light: #e2531f;
    --back-red: #c8231f;
    --back-red-deep: #8e1016;
    --contact-ink: #f6dccf;
  }
  html, body {
    margin: 0;
    padding: 0;
    width: 1200px;
    height: 969px;
    overflow: hidden;
    background: var(--page-bg);
  }
  .canvas {
    position: relative;
    width: 1200px;
    height: 969px;
  }
  .card {
    position: absolute;
    top: 228px;
    height: 532px;
    box-shadow: 0 6px 22px rgba(0,0,0,0.18);
  }
  .card-front {
    left: 150px;
    width: 424px;
    background: linear-gradient(180deg, #f6f5f3 0%, var(--card-front) 60%, #ece6e2 100%);
    border: 1px solid var(--card-front-edge);
    box-sizing: border-box;
  }
  .brand {
    position: absolute;
    left: 44px;
    top: 282px;
    display: flex;
    align-items: center;
    gap: 14px;
  }
  .brand-mark {
    width: 18px;
    height: 18px;
    background: var(--brand-red);
    flex: none;
  }
  .brand-name {
    font-family: "Questrial", sans-serif;
    font-size: 27px;
    line-height: 34px;
    color: var(--ink-dark);
    margin: 0;
    font-weight: 400;
  }
  .card-back {
    left: 586px;
    width: 500px;
    overflow: hidden;
  }
  .back-art {
    position: absolute;
    inset: 0;
    background:
      radial-gradient(ellipse at 75% 20%, rgba(236,110,30,0.85) 0%, rgba(236,110,30,0) 55%),
      radial-gradient(ellipse at 30% 85%, rgba(110,8,14,0.75) 0%, rgba(110,8,14,0) 55%),
      linear-gradient(160deg, var(--back-red-light) 0%, var(--back-red) 50%, var(--back-red-deep) 100%);
  }
  .contact-list {
    position: absolute;
    left: 38px;
    top: 226px;
    margin: 0;
    padding: 0;
    list-style: none;
    font-family: "Arimo", sans-serif;
    font-size: 20px;
    color: var(--contact-ink);
  }
  .contact-list li {
    display: flex;
    align-items: center;
    height: 28px;
  }
  .contact-list svg {
    width: 16px;
    height: 16px;
    margin-right: 18px;
    fill: var(--contact-ink);
    flex: none;
  }
</style>
</head>
<body>
<main class="canvas">
  <section class="card card-front" aria-label="Card front">
    <div class="brand">
      <span class="brand-mark"></span>
      <h1 class="brand-name">Light for the Weary Souls</h1>
    </div>
  </section>

  <section class="card card-back" aria-label="Card back">
    <div class="back-art" role="img" aria-label="Layered translucent red and orange angular shapes"></div>
    <ul class="contact-list">
      <li>
        <svg viewBox="0 0 16 16" aria-hidden="true"><path d="M3.2 1.2l2.4-.4 1.4 3.4-1.6 1.2c.8 1.8 2 3 3.8 3.8l1.2-1.6 3.4 1.4-.4 2.4c-.2 1-1 1.6-2 1.6C6 13 3 10 2.4 4.2c-.1-1 .3-2.8.8-3z"/></svg>
        555-382-7194
      </li>
      <li>
        <svg viewBox="0 0 16 16" aria-hidden="true"><path d="M1 3h14v10H1z M2.5 4.5v.4L8 9l5.5-4.1v-.4z" fill-rule="evenodd"/></svg>
        email@lightfortheweary-mail.org
      </li>
      <li>
        <svg viewBox="0 0 16 16" aria-hidden="true"><circle cx="8" cy="8" r="7"/><path d="M4 4.5c1.5 0 2 1 3 1.5s.5 2-.5 2.5S6 11 5 12c-1-1.5-2-3.5-1-7.5zM10 3c1 .5 2.5 2 2.5 4-1 .5-2 0-2.5 1s.5 2.5-.5 4c-1-1-1-2.5-1.5-3.5S9 5 10 3z" fill="#c8231f"/></svg>
        www.lightfortheweary-mail.org
      </li>
    </ul>
  </section>
</main>
</body>
</html>
```